Dew Petal Ritual. Home based organic skin care manufacturer

We need top notch user friendly and interactive web6/mobile site that will cater to online e commerce, retail of our varieties of products and real time communication with online buyers.

Coding

Coded - Design and coding required

Number of Pages Required

1 page

```html
<!DOCTYPE html>
<html lang="en">
<head>
<meta charset="utf-8">
<title>Dew Petal Ritual — Organic Skin Care</title>
<link rel="stylesheet" href="https://fonts.googleapis.com/css2?family=Jost:wght@400;500;600&family=Lato:wght@400;700&display=swap">
<style>
:root{
  --rose:#a9766c;
  --rose-dark:#8f5f57;
  --hero:#c3928b;
  --blush:#e6b8b3;
  --soft:#f3f3f3;
  --ink:#2a2a2a;
  --muted:#6b6b6b;
  --footer:#2d2426;
  --white:#ffffff;
  --gold:#f2b600;
}
*{margin:0;padding:0;box-sizing:border-box}
html,body{width:1200px;height:3530px;overflow:hidden}
body{position:relative;background:var(--white);font-family:"Jost",sans-serif;color:var(--ink)}
.abs{position:absolute}
a{color:inherit;text-decoration:none}

/* Hero */
.hero{left:0;top:0;width:1200px;height:641px;background:linear-gradient(180deg,#c29089 0%,#c99a92 60%,#cfa39b 100%)}
.brand{font-family:"Jost",sans-serif;font-weight:500;color:var(--white);font-size:20px;letter-spacing:2px;display:flex;align-items:center;gap:10px}
.brand-dot{width:12px;height:12px;border-radius:50%;background:currentColor;display:inline-block}
.nav a{position:absolute;top:34px;font-size:15px;color:var(--white)}
.cart-badge{left:1054px;top:28px;width:36px;height:36px;border-radius:50%;background:var(--blush)}
.hero-title{left:111px;top:258px;font-size:56px;font-weight:600;color:var(--white);letter-spacing:.5px}
.hero-sub{left:111px;top:330px;font-size:19px;color:var(--white);font-family:"Lato",sans-serif}
.btn{display:flex;align-items:center;justify-content:center;border-radius:26px;font-weight:600;font-size:15px;letter-spacing:.5px}
.btn-solid{background:var(--rose);color:var(--white)}
.hero-btn{left:111px;top:377px;width:145px;height:50px}
.hero-visual{left:590px;top:92px;width:486px;height:486px;border-radius:50%;background:radial-gradient(circle at 50% 45%,#f4f1ef 0%,#e9dedb 45%,#d7a49f 46%,#d29c96 100%)}

/* Categories */
.cat{top:705px;width:305px;height:369px;background:linear-gradient(180deg,#e4e4e4 0%,#a9a9a9 55%,#3c3c3c 100%);display:flex;flex-direction:column;align-items:center;justify-content:flex-end;padding-bottom:30px;color:var(--white)}
.cat .tag{font-size:13px;font-weight:600;color:#d9a59c;text-transform:uppercase}
.cat .name{font-size:21px;font-weight:500;letter-spacing:1px;text-transform:uppercase}
.cat-shop{margin-top:18px;width:130px;height:42px;font-size:14px}

/* Products */
.products{left:0;top:1165px;width:1200px;height:590px;background:var(--soft)}
.section-title{font-size:35px;font-weight:500;color:var(--ink);width:1200px;text-align:center}
.product{top:1311px;width:235px;height:295px;background:var(--white)}
.product-img{position:absolute;left:50%;top:50%;transform:translate(-50%,-50%);width:90px;height:170px;border-radius:14px}
.p-name{top:1626px;font-size:15px;font-weight:500}
.p-price{top:1655px;font-size:19px;font-weight:500;color:var(--rose)}
.p-heart{top:1627px}
.arrow{top:1434px;width:44px;height:44px;border-radius:50%;border:1px solid #bdbdbd;background:var(--white);display:flex;align-items:center;justify-content:center}

/* Testimonial */
.testimonial{left:0;top:1755px;width:1200px;height:428px;background:linear-gradient(90deg,#ecc6be 0%,#dfa8a2 50%,#efc9c4 100%)}
.t-photo{left:140px;top:1810px;width:312px;height:318px;border-radius:28px;background:linear-gradient(180deg,#dcdcdc 0%,#b9b3ae 60%,#3b3b3d 100%)}
.t-title{left:500px;top:1802px;font-size:36px;font-weight:500;color:var(--white)}
.stars{left:503px;top:1852px;display:flex;gap:3px}
.t-text{left:504px;top:1881px;width:560px;font-family:"Lato",sans-serif;font-size:14.5px;line-height:26.7px;color:var(--white)}
.t-name{left:504px;top:2024px;font-size:19px;font-weight:500;color:var(--white)}
.t-loc{left:504px;top:2056px;font-size:13px;color:var(--white);font-family:"Lato",sans-serif}
.dots{left:503px;top:2101px;display:flex;gap:4px}
.dots span{width:11px;height:11px;border-radius:50%;border:1px solid var(--white)}
.dots span.on{background:var(--white)}

/* Features */
.feature{width:391px;height:155px;background:var(--white);box-shadow:0 4px 22px rgba(0,0,0,.07);border-radius:0 8px 8px 0}
.feature-icon{position:absolute;left:0;top:0;width:117px;height:155px;background:var(--rose);border-radius:0 78px 78px 0;display:flex;align-items:center;justify-content:center}
.feature h3{position:absolute;left:132px;top:26px;font-size:18px;font-weight:500;letter-spacing:.3px}
.feature p{position:absolute;left:132px;top:58px;width:245px;font-family:"Lato",sans-serif;font-size:15.5px;line-height:26.5px;color:var(--muted)}

/* CTA */
.cta{left:0;top:2701px;width:1200px;height:291px;background:linear-gradient(90deg,#b07d74 0%,#c99a92 50%,#b7847b 100%)}
.cta-title{top:2766px;font-size:36px;font-weight:500;color:var(--white);width:1200px;text-align:center}
.cta-retail{left:441px;top:2847px;width:132px;height:51px;background:var(--white);color:var(--rose);font-size:15px}
.cta-buyer{left:614px;top:2847px;width:144px;height:51px;border:2px solid var(--white);color:var(--white);font-size:15px}

/* Footer */
.footer{left:0;top:2992px;width:1200px;height:538px;background:var(--footer)}
.nl-title{left:452px;top:3040px;font-size:35px;font-weight:500;color:var(--white)}
.nl-input{left:453px;top:3114px;width:435px;height:55px;border:1px solid #d6d6d6;color:var(--white);font-size:15px;padding-left:36px;display:flex;align-items:center;font-family:"Lato",sans-serif}
.nl-btn{left:888px;top:3114px;width:181px;height:55px;background:var(--rose);color:var(--white);font-size:16px;font-weight:600;display:flex;align-items:center;justify-content:center}
.f-head{top:3217px;font-size:19px;font-weight:500;color:var(--white)}
.f-list{top:3252px;font-family:"Lato",sans-serif;font-size:15px;line-height:26px;color:var(--white);list-style:none}
.f-about{left:128px;top:3252px;width:270px;font-family:"Lato",sans-serif;font-size:14.5px;line-height:23.5px;color:var(--white)}
.pay{top:3347px;width:50px;height:33px;background:var(--white);border-radius:4px;display:flex;align-items:center;justify-content:center}
.pay i{display:block;width:30px;height:12px;border-radius:2px}
.social{top:3259px;width:30px;height:30px;border-radius:50%;background:var(--white);display:flex;align-items:center;justify-content:center}
.social i{display:block;width:10px;height:10px;border-radius:50%;background:var(--footer)}
.divider{left:110px;top:3435px;width:980px;height:1px;background:#4a4044}
.copy{top:3466px;width:1200px;text-align:center;font-family:"Lato",sans-serif;font-size:15px;color:var(--white)}
</style>
</head>
<body>

<!-- Hero -->
<section class="abs hero" role="img" aria-label="Soft rose backdrop with blurred green foliage"></section>
<div class="abs brand" style="left:110px;top:52px"><span class="brand-dot"></span>Dew Petal Ritual</div>
<nav class="nav">
  <a style="left:363px">Home</a>
  <a style="left:438px">About Us</a>
  <a style="left:537px">Shop</a>
  <a style="left:608px">Blog</a>
  <a style="left:674px">Distributors</a>
  <a style="left:792px">Contacts</a>
  <a style="left:934px;top:37px">Login</a>
  <a style="left:988px;top:37px">|</a>
  <a style="left:1007px;top:37px">Cart</a>
</nav>
<div class="abs cart-badge"></div>
<svg class="abs" style="left:1062px;top:37px" width="20" height="18" viewBox="0 0 20 18"><path d="M1 2h3l2 9h10l2-7H6" fill="none" stroke="#fff" stroke-width="2"/><circle cx="8" cy="15" r="1.6" fill="#fff"/><circle cx="15" cy="15" r="1.6" fill="#fff"/></svg>
<svg class="abs" style="left:1074px;top:52px" width="12" height="12"><circle cx="6" cy="6" r="5" fill="#fff" opacity=".7"/></svg>

<h1 class="abs hero-title">Skin Made Perfect</h1>
<p class="abs hero-sub">Give your skin the new look and feel it deserves.</p>
<a class="abs btn btn-solid hero-btn">SHOP NOW</a>
<div class="abs hero-visual" role="img" aria-label="Jar of brightening body milk in a rose circle"></div>

<!-- Categories -->
<div class="abs cat" style="left:114px" role="img" aria-label="Hair care bottles in black and red">
  <span class="tag">Most Popular</span><span class="name">Hair Care</span>
</div>
<div class="abs cat" style="left:447px" role="img" aria-label="Facial soap bars stacked">
  <span class="tag">Most Popular</span><span class="name">Facials</span>
  <a class="btn btn-solid cat-shop">SHOP NOW</a>
</div>
<div class="abs cat" style="left:780px" role="img" aria-label="Amber bottles of body wash and serum">
  <span class="tag">Most Popular</span><span class="name">Baths</span>
</div>

<!-- Products -->
<section class="abs products"></section>
<h2 class="abs section-title" style="left:0;top:1218px">Our Products</h2>

<div class="abs arrow" style="left:33px"><svg width="10" height="10"><path d="M7 1L3 5l4 4" fill="none" stroke="#333" stroke-width="1.5"/></svg></div>
<div class="abs arrow" style="left:1127px"><svg width="10" height="10"><path d="M3 1l4 4-4 4" fill="none" stroke="#333" stroke-width="1.5"/></svg></div>

<div class="abs product" style="left:108px"><div class="product-img" role="img" aria-label="White tub of brightening body milk" style="background:linear-gradient(180deg,#f2f2f2,#d8d8e2)"></div></div>
<div class="abs product" style="left:356px"><div class="product-img" role="img" aria-label="Slim bottle of kiddies soap" style="width:50px;background:linear-gradient(180deg,#f4f4f8,#d9d4ea)"></div>
  <a class="btn btn-solid abs" style="left:70px;top:134px;width:102px;height:34px;font-size:11px">SHOP NOW</a></div>
<div class="abs product" style="left:605px"><div class="product-img" role="img" aria-label="Amber dropper bottle of serum" style="width:50px;background:linear-gradient(180deg,#3a2a22,#9a4d2a)"></div></div>
<div class="abs product" style="left:853px"><div class="product-img" role="img" aria-label="Yellow jar of face cream" style="width:100px;height:90px;background:linear-gradient(180deg,#fbf3d8,#f2b740)"></div></div>

<span class="abs p-name" style="left:108px">Stretch Marks Cream</span>
<span class="abs p-name" style="left:356px">Kiddies Soap</span>
<span class="abs p-name" style="left:605px">Stretch Marks Cream</span>
<span class="abs p-name" style="left:853px">Stretch Marks Cream</span>
<svg class="abs p-heart" style="left:324px" width="16" height="14" viewBox="0 0 16 14"><path d="M8 13L2 7a3.3 3.3 0 016-4 3.3 3.3 0 016 4z" fill="none" stroke="#555" stroke-width="1.3"/></svg>
<svg class="abs p-heart" style="left:572px" width="16" height="14" viewBox="0 0 16 14"><path d="M8 13L2 7a3.3 3.3 0 016-4 3.3 3.3 0 016 4z" fill="none" stroke="#555" stroke-width="1.3"/></svg>
<svg class="abs p-heart" style="left:821px" width="16" height="14" viewBox="0 0 16 14"><path d="M8 13L2 7a3.3 3.3 0 016-4 3.3 3.3 0 016 4z" fill="none" stroke="#555" stroke-width="1.3"/></svg>
<svg class="abs p-heart" style="left:1069px" width="16" height="14" viewBox="0 0 16 14"><path d="M8 13L2 7a3.3 3.3 0 016-4 3.3 3.3 0 016 4z" fill="none" stroke="#555" stroke-width="1.3"/></svg>
<span class="abs p-price" style="left:108px">$0.00</span>
<span class="abs p-price" style="left:356px">$0.00</span>
<span class="abs p-price" style="left:605px">$0.00</span>
<span class="abs p-price" style="left:853px">$0.00</span>

<!-- Testimonial -->
<section class="abs testimonial" role="img" aria-label="Soft pink backdrop with dried flowers and cream"></section>
<div class="abs t-photo" role="img" aria-label="Portrait of a customer"></div>
<h2 class="abs t-title">What People Say</h2>
<div class="abs stars">
  <svg width="14" height="14" viewBox="0 0 14 14"><path d="M7 0l2 5h5l-4 3 1.5 5L7 10l-4.5 3L4 8 0 5h5z" fill="#f2b600"/></svg>
  <svg width="14" height="14" viewBox="0 0 14 14"><path d="M7 0l2 5h5l-4 3 1.5 5L7 10l-4.5 3L4 8 0 5h5z" fill="#f2b600"/></svg>
  <svg width="14" height="14" viewBox="0 0 14 14"><path d="M7 0l2 5h5l-4 3 1.5 5L7 10l-4.5 3L4 8 0 5h5z" fill="#f2b600"/></svg>
  <svg width="14" height="14" viewBox="0 0 14 14"><path d="M7 0l2 5h5l-4 3 1.5 5L7 10l-4.5 3L4 8 0 5h5z" fill="#f2b600"/></svg>
  <svg width="14" height="14" viewBox="0 0 14 14"><path d="M7 0l2 5h5l-4 3 1.5 5L7 10l-4.5 3L4 8 0 5h5z" fill="#f2b600"/></svg>
</div>
<p class="abs t-text">"I used a harsh expensive product that ruined my skin. I didn't know it will clear until I tried Dew Petal Ritual products. They were not harsh on my skin at all. With time all the dark patches on my skin and white patches on my face cleared. The glow is mild-blowing and I thank God I gave DPR a chance! Even my legs and feet are very bright too. I trust DPR with my skin".</p>
<span class="abs t-name">Adaeze Okonkwo</span>
<span class="abs t-loc">(Texas, USA)</span>
<div class="abs dots"><span></span><span class="on"></span><span></span><span></span><span></span></div>

<!-- Features -->
<div class="abs feature" style="left:160px;top:2265px">
  <div class="feature-icon"><svg width="90" height="60" viewBox="0 0 90 60" fill="none" stroke="#fff" stroke-width="2.5"><path d="M22 12h38v32H22zM60 22h14l8 10v12H60"/><circle cx="34" cy="48" r="5"/><circle cx="70" cy="48" r="5"/><path d="M4 22h14M8 30h12M4 38h14"/></svg></div>
  <h3>FAST &amp; PROMPT DELIVERY</h3>
  <p>Lorem ipsum dolor sit amet, consectetur adipiscing elit, sed do eiusmod incididunt</p>
</div>
<div class="abs feature" style="left:649px;top:2265px">
  <div class="feature-icon"><svg width="76" height="70" viewBox="0 0 76 70" fill="none" stroke="#fff" stroke-width="2.5"><path d="M38 4l16 6v12c0 10-7 17-16 21-9-4-16-11-16-21V10z"/><path d="M31 23l5 5 9-9"/><path d="M6 44h10v22H6zM16 48l14 0 12 6h16a5 5 0 010 8H30"/></svg></div>
  <h3>SECURE PAYMENT</h3>
  <p>Lorem ipsum dolor sit amet, consectetur adipiscing elit, sed do eiusmod incididunt</p>
</div>
<div class="abs feature" style="left:160px;top:2452px">
  <div class="feature-icon"><svg width="76" height="76" viewBox="0 0 76 76" fill="none" stroke="#fff" stroke-width="2.5"><circle cx="38" cy="38" r="32" stroke-dasharray="4 3"/><circle cx="38" cy="38" r="24"/><path d="M20 38h36M24 30h28M24 46h28"/></svg></div>
  <h3>100% GUARANTEED</h3>
  <p>Lorem ipsum dolor sit amet, consectetur adipiscing elit, sed do eiusmod incididunt</p>
</div>
<div class="abs feature" style="left:649px;top:2452px">
  <div class="feature-icon"><svg width="76" height="70" viewBox="0 0 76 70" fill="none" stroke="#fff" stroke-width="2.5"><path d="M30 10h36v22H30z"/><circle cx="48" cy="21" r="5"/><path d="M20 14a22 22 0 000 30M16 40l4 4 4-4"/><path d="M6 44h10v22H6zM16 48l14 0 12 6h16a5 5 0 010 8H30"/></svg></div>
  <h3>MONEY BACK GUARANTEED</h3>
  <p>Lorem ipsum dolor sit amet, consectetur adipiscing elit, sed do eiusmod incididunt</p>
</div>

<!-- CTA -->
<section class="abs cta" role="img" aria-label="Smiling woman touching her glowing skin, rose tinted"></section>
<h2 class="abs cta-title" style="left:0">Real-Time Communication With Online Buyers</h2>
<a class="abs btn cta-retail">RETAIL</a>
<a class="abs btn cta-buyer">BUYER</a>

<!-- Footer -->
<footer class="abs footer"></footer>
<div class="abs brand" style="left:162px;top:3094px"><span class="brand-dot"></span>Dew Petal Ritual</div>
<h2 class="abs nl-title">Sign Up Our Newsletter</h2>
<div class="abs nl-input">Enter Your Email</div>
<a class="abs nl-btn">Subscribe</a>

<h4 class="abs f-head" style="left:126px">Accepted Payment Methods</h4>
<p class="abs f-about">Lorem ipsum dolor sit amet, consec-tetur adipiscing elit, sed do eiusmod tempor incididunt ut labore</p>
<div class="abs pay" style="left:129px"><i style="background:#1a3b8f"></i></div>
<div class="abs pay" style="left:184px"><i style="background:#e0552c"></i></div>
<div class="abs pay" style="left:239px"><i style="background:#2a73c9"></i></div>
<div class="abs pay" style="left:294px"><i style="background:#9a9a9a"></i></div>
<div class="abs pay" style="left:349px"><i style="background:#111"></i></div>

<h4 class="abs f-head" style="left:460px">Quick Link</h4>
<ul class="abs f-list" style="left:462px">
  <li>Home</li><li>About Us</li><li>Shop</li><li>Blog</li><li>Distributors</li><li>Contacts</li>
</ul>

<h4 class="abs f-head" style="left:659px">Help Link</h4>
<ul class="abs f-list" style="left:661px;line-height:30px">
  <li>Support / Contact</li><li>Privacy Policies</li><li>Terms of use</li><li>Return Policy</li>
</ul>

<h4 class="abs f-head" style="left:886px">Follow Us</h4>
<div class="abs social" style="left:885px;background:#e7b0a8"><i style="background:#fff"></i></div>
<div class="abs social" style="left:924px"><i></i></div>
<div class="abs social" style="left:963px"><i></i></div>
<div class="abs social" style="left:1002px"><i></i></div>

<div class="abs divider"></div>
<p class="abs copy" style="left:0">© Copyrights 2023&nbsp; Dew Petal Ritual &nbsp; | &nbsp; All Rights Reserved</p>

</body>
</html>
```